Business Card Design

We need a design for business cards for our company. We have a logo. We teach EMT's and we are based out of Virginia. The information that will need to add would be, name, title, phone number, email, address. On the back of the business card would be "We help you, help others"

Target Market(s)

People that want to become EMT's

Colors

Designer to choose colors to be used in the design.

Requirements
Must have
• company logo

```html
<!DOCTYPE html>
<html lang="en">
<head>
<meta charset="utf-8">
<title>Rescue Path Academy – Business Cards</title>
<link href="https://fonts.googleapis.com/css2?family=Work+Sans:wght@400;600;700&display=swap" rel="stylesheet">
<style>
  :root {
    --stage: #b9b9b9;
    --navy: #26303b;
    --red: #c01f2f;
    --white: #ffffff;
    --grey-band: #a3a6aa;
    --brand-red: #d8293b;
    --text-light: #ffffff;
  }
  html, body {
    margin: 0;
    padding: 0;
    width: 1200px;
    height: 930px;
    overflow: hidden;
    background: var(--stage);
    font-family: "Work Sans", Arial, sans-serif;
  }
  .canvas {
    position: relative;
    width: 1200px;
    height: 930px;
  }
  .card {
    position: absolute;
    width: 540px;
    height: 310px;
    border-radius: 22px;
    overflow: hidden;
    box-shadow: 0 10px 24px rgba(0,0,0,0.25);
  }
  .card--back {
    left: 110px;
    top: 110px;
    background: var(--navy);
    display: flex;
    align-items: center;
    justify-content: center;
  }
  .card--front {
    left: 560px;
    top: 500px;
    background: var(--red);
  }
  .card__shape {
    position: absolute;
    inset: 0;
  }
  .brand {
    display: flex;
    align-items: center;
    gap: 10px;
    font-weight: 700;
    color: var(--brand-red);
    letter-spacing: 0.5px;
    text-transform: uppercase;
  }
  .brand__dot {
    width: 14px;
    height: 14px;
    border-radius: 50%;
    background: var(--brand-red);
  }
  .card--back .brand { font-size: 30px; }
  .card--front .brand {
    position: absolute;
    top: 52px;
    right: 34px;
    font-size: 24px;
  }
  .contact {
    position: absolute;
    left: 34px;
    bottom: 26px;
    color: var(--text-light);
    font-size: 15px;
    line-height: 1.35;
  }
  .contact__name {
    font-weight: 700;
    font-size: 22px;
    letter-spacing: 0.5px;
    text-transform: uppercase;
    margin: 0;
  }
  .contact__title { margin: 0 0 10px 14px; }
  .contact__address { margin: 0 0 6px 34px; }
  .contact__line {
    display: flex;
    align-items: center;
    gap: 8px;
    margin-left: 62px;
  }
  .contact__icon { width: 11px; height: 11px; flex: none; }
</style>
</head>
<body>
<main class="canvas">

  <section class="card card--back">
    <div class="brand"><span class="brand__dot"></span>Rescue Path Academy</div>
  </section>

  <section class="card card--front">
    <svg class="card__shape" viewBox="0 0 540 310" preserveAspectRatio="none" aria-hidden="true">
      <path d="M128,0 C150,150 330,240 540,222" fill="none" stroke="var(--grey-band)" stroke-width="12"/>
      <path d="M142,0 H540 V214 C340,232 168,150 142,0 Z" fill="var(--white)"/>
    </svg>

    <div class="brand"><span class="brand__dot"></span>Rescue Path Academy</div>

    <div class="contact">
      <p class="contact__name">Daniel Hart</p>
      <p class="contact__title">Director</p>
      <p class="contact__address">418 Harbor St.<br>Riverton, VA 23140</p>
      <div class="contact__line">
        <svg class="contact__icon" viewBox="0 0 24 24" aria-hidden="true"><path fill="#fff" d="M6.6 10.8a15.1 15.1 0 0 0 6.6 6.6l2.2-2.2c.3-.3.7-.4 1-.2 1.1.4 2.3.6 3.6.6.6 0 1 .4 1 1V20c0 .6-.4 1-1 1A17 17 0 0 1 3 4c0-.6.4-1 1-1h3.5c.6 0 1 .4 1 1 0 1.3.2 2.5.6 3.6.1.3 0 .7-.2 1z"/></svg>
        <span>555-204-7788</span>
      </div>
      <div class="contact__line" style="margin-left:72px">
        <svg class="contact__icon" viewBox="0 0 24 24" aria-hidden="true"><rect x="2" y="5" width="20" height="14" rx="2" fill="none" stroke="#fff" stroke-width="2"/><path d="M2 6l10 7 10-7" fill="none" stroke="#fff" stroke-width="2"/></svg>
        <span>info@rescuepath.com</span>
      </div>
      <div class="contact__line" style="margin-left:82px">
        <svg class="contact__icon" viewBox="0 0 24 24" aria-hidden="true"><circle cx="12" cy="12" r="10" fill="none" stroke="#fff" stroke-width="2"/><path d="M2 12h20M12 2c3 3 3 17 0 20M12 2c-3 3-3 17 0 20" fill="none" stroke="#fff" stroke-width="2"/></svg>
        <span>www.rescuepath.com</span>
      </div>
    </div>
  </section>

</main>
</body>
</html>
```